Business Card Design

We need the business card for our new business based in St. Marys, we manufacture mainly bubble wraps. And we would like the design to use our company logo and also make it easy for people to understand right away we are bubble wrap manufacturer

Industry/Entity Type

Business

Contact Information for Business Card

Cushtane Pty Ltd, 14 Larkin Road St. Marys NSW 2760, Tel: 02 9471 5826, Fax: 9471 5839, Dara Oyelaran, General Manager, Mobile :0438 217 564, dara.oyelaran@cushtane.com.au, Website: cushtane.com.au

```html
<!DOCTYPE html>
<html lang="en">
<head>
<meta charset="utf-8">
<title>Cushtane Pty Ltd – Business Card</title>
<link rel="stylesheet" href="https://fonts.googleapis.com/css2?family=Titillium+Web:wght@300;400;600;700&display=swap">
<style>
  :root {
    --bg: #e4e2df;
    --card-white: #f4f4f4;
    --band-grey: #6e6e6e;
    --band-dark: #5c5c5c;
    --ink: #4a4a4a;
    --ink-soft: #7a7a7a;
    --accent: #d3262b;
    --white: #ffffff;
  }
  * { box-sizing: border-box; margin: 0; padding: 0; }
  html, body { width: 1200px; height: 885px; overflow: hidden; }
  body {
    background: var(--bg);
    font-family: "Titillium Web", Arial, sans-serif;
    color: var(--ink);
  }
  .canvas {
    position: relative;
    width: 1200px;
    height: 885px;
  }
  .card {
    position: absolute;
    left: 320px;
    width: 560px;
    height: 320px;
    border-radius: 16px;
    overflow: hidden;
    background: var(--card-white);
    box-shadow: 0 6px 18px rgba(0,0,0,0.18);
  }
  .card--front { top: 95px; }
  .card--back { top: 470px; }
  .card__bands { position: absolute; inset: 0; width: 100%; height: 100%; }

  .brand { position: absolute; }
  .brand__name {
    display: block;
    font-weight: 700;
    color: var(--ink);
    letter-spacing: 1px;
    line-height: 1;
  }
  .brand__mark {
    display: inline-block;
    background: var(--accent);
    vertical-align: middle;
  }
  .brand__tagline {
    display: block;
    font-weight: 400;
    text-transform: uppercase;
    color: var(--ink-soft);
  }

  /* front */
  .card--front .brand {
    left: 0; right: 0; top: 112px;
    text-align: center;
  }
  .card--front .brand__row { display: flex; align-items: center; justify-content: center; gap: 12px; }
  .card--front .brand__mark { width: 22px; height: 22px; }
  .card--front .brand__name { font-size: 62px; }
  .card--front .brand__tagline { font-size: 11.5px; letter-spacing: 5.2px; margin-top: 6px; }

  /* back */
  .card--back .brand { left: 34px; top: 30px; }
  .card--back .brand__row { display: flex; align-items: center; gap: 8px; }
  .card--back .brand__mark { width: 14px; height: 14px; }
  .card--back .brand__name { font-size: 40px; }
  .card--back .brand__tagline { font-size: 8px; letter-spacing: 3.6px; margin-top: 4px; }

  .person {
    position: absolute;
    right: 0; top: 40px;
    width: 210px;
    padding: 8px 18px 9px;
    background: var(--band-dark);
    color: var(--white);
  }
  .person__name { font-size: 21px; font-weight: 400; line-height: 1.1; }
  .person__role { font-size: 13px; font-weight: 300; }

  .contact-list { position: absolute; list-style: none; }
  .contact-list--phones { left: 34px; top: 132px; }
  .contact-list--online { left: 290px; top: 140px; }
  .contact-list li {
    display: flex; align-items: center; gap: 8px;
    font-size: 16px; line-height: 24px; color: var(--ink);
  }
  .contact-list--online li { font-size: 13px; line-height: 20px; }
  .icon { width: 13px; height: 13px; flex: none; }

  .address {
    position: absolute;
    left: 34px; bottom: 22px;
    font-size: 16px; font-weight: 400;
    color: var(--white);
    letter-spacing: 0.3px;
  }
</style>
</head>
<body>
<main class="canvas">

  <section class="card card--front" aria-label="Business card front">
    <svg class="card__bands" viewBox="0 0 560 320" aria-hidden="true">
      <rect width="560" height="320" fill="var(--band-grey)"/>
      <path d="M0 78 Q280 128 560 78 L560 246 Q280 196 0 246 Z" fill="var(--card-white)"/>
      <path d="M0 60 Q280 112 560 60" fill="none" stroke="var(--white)" stroke-width="4"/>
      <path d="M0 264 Q280 212 560 264" fill="none" stroke="var(--white)" stroke-width="4"/>
      <path d="M0 46 Q280 100 560 46" fill="none" stroke="#8a8a8a" stroke-width="2"/>
      <path d="M0 278 Q280 224 560 278" fill="none" stroke="#8a8a8a" stroke-width="2"/>
    </svg>
    <div class="brand">
      <div class="brand__row">
        <span class="brand__mark"></span>
        <span class="brand__name">CUSHTANE</span>
      </div>
      <span class="brand__tagline">Protective Packaging Solutions</span>
    </div>
  </section>

  <section class="card card--back" aria-label="Business card back">
    <svg class="card__bands" viewBox="0 0 560 320" aria-hidden="true">
      <rect width="560" height="320" fill="var(--card-white)"/>
      <path d="M0 256 Q280 236 560 262 L560 320 L0 320 Z" fill="var(--band-grey)"/>
      <path d="M0 244 Q280 222 560 250" fill="none" stroke="var(--band-grey)" stroke-width="4"/>
      <path d="M0 236 Q280 212 560 242" fill="none" stroke="#9a9a9a" stroke-width="1.5"/>
    </svg>

    <div class="brand">
      <div class="brand__row">
        <span class="brand__mark"></span>
        <span class="brand__name">CUSHTANE</span>
      </div>
      <span class="brand__tagline">Protective Packaging Solutions</span>
    </div>

    <div class="person">
      <p class="person__name">Dara Oyelaran</p>
      <p class="person__role">General Manager</p>
    </div>

    <ul class="contact-list contact-list--phones">
      <li>
        <svg class="icon" viewBox="0 0 13 13" aria-label="Telephone"><rect width="13" height="13" fill="var(--accent)"/><path d="M3.5 3 L5 3 L5.6 5 L4.8 5.6 Q5.6 7.4 7.4 8.2 L8 7.4 L10 8 L10 9.5 Q5 10 3.5 3Z" fill="var(--white)"/></svg>
        02 9471 5826
      </li>
      <li>
        <svg class="icon" viewBox="0 0 13 13" aria-label="Mobile"><rect width="13" height="13" fill="var(--accent)"/><rect x="4.5" y="2.5" width="4" height="8" rx="0.8" fill="var(--white)"/></svg>
        0438 217 564
      </li>
      <li>
        <svg class="icon" viewBox="0 0 13 13" aria-label="Fax"><rect width="13" height="13" fill="var(--accent)"/><rect x="3" y="5" width="7" height="4.5" fill="var(--white)"/><rect x="4.5" y="2.5" width="4" height="2.5" fill="var(--white)"/></svg>
        9471 5839
      </li>
    </ul>

    <ul class="contact-list contact-list--online">
      <li>
        <svg class="icon" viewBox="0 0 13 13" aria-label="Website"><rect width="13" height="13" fill="var(--accent)"/><circle cx="6.5" cy="6.5" r="3.8" fill="none" stroke="var(--white)" stroke-width="1"/><path d="M2.7 6.5 H10.3 M6.5 2.7 V10.3" stroke="var(--white)" stroke-width="0.8"/></svg>
        cushtane.com.au
      </li>
      <li>
        <svg class="icon" viewBox="0 0 13 13" aria-label="Email"><rect width="13" height="13" fill="var(--accent)"/><rect x="2.5" y="3.5" width="8" height="6" fill="var(--white)"/><path d="M2.5 3.5 L6.5 7 L10.5 3.5" fill="none" stroke="var(--accent)" stroke-width="0.9"/></svg>
        dara.oyelaran@cushtane.com.au
      </li>
    </ul>

    <p class="address">14 Larkin Road Ravenwood NSW 2793</p>
  </section>

</main>
</body>
</html>
```